Bram Keystone Homes needs a business card

We need a business card for a new company in Canada, Ontario. Our company is all about luxury contraction homes for our clients. Our product and services are custom projects design. Under the business logo that will be created, we want a slogan that will be a memorable phrase for consumers to remember us to tell their friends and relatives.

Additional infomation
- Ludovic Entrasse
- President / Ceo
-519.604.3087

Find point what luxury construction products and services can be done

We like to see colors:
- #663300
- and something other colors or color that would attract the client needs and wants

The final design should communicate leads from new or old clients that will grow our empire. Most of all, we try to work among the budget that clients want

NOTE
- we also need an icon for the business (Example: Instagram, Facebook, and Whatsapp icons)
- We want the company name to be remembered easily for clients and our distributors who would get our orders.
- we need an icon on the business cards: Facebook and Instagram.

Thanks,
Bram Keystone Homes

```html
<!DOCTYPE html>
<html lang="en">
<head>
<meta charset="utf-8">
<title>Bram Keystone Homes – Business Card</title>
<link href="https://fonts.googleapis.com/css2?family=Alfa+Slab+One&family=Archivo:wght@400;500;700&display=swap" rel="stylesheet">
<style>
  :root{
    --brown-deep:#663300;
    --paper:#ffffff;
    --paper-shade:#e6e6e6;
    --rim-grey:#a9a9a9;
    --stage:#eeeae5;
    --ink-light:#ffffff;
  }
  *{margin:0;padding:0;box-sizing:border-box}
  html,body{width:1200px;height:780px;overflow:hidden}
  body{
    background:var(--stage);
    font-family:"Archivo",Arial,sans-serif;
    display:flex;align-items:center;justify-content:center;gap:34px;
  }
  .card{
    position:relative;width:560px;height:320px;border-radius:14px;overflow:hidden;
    box-shadow:0 10px 28px rgba(60,35,10,.22);
  }
  .card-bg{position:absolute;inset:0}
  .brand{position:absolute;white-space:nowrap}
  .brand-name{
    font-family:"Alfa Slab One",Georgia,serif;
    color:var(--brown-deep);font-size:30px;line-height:1;letter-spacing:.2px;
  }
  .brand-slogan{
    color:var(--brown-deep);font-weight:500;font-size:11.5px;letter-spacing:.2px;margin-top:7px;text-align:center;
  }

  /* front */
  .front .brand{left:46px;top:78px}
  .person{position:absolute;right:276px;top:236px;color:var(--ink-light);text-align:right;white-space:nowrap}
  .person-name{font-size:19px;font-weight:700;letter-spacing:.2px}
  .person-role{font-size:12.5px;margin-top:4px;opacity:.92}
  .divider{position:absolute;left:296px;top:234px;width:1.5px;height:46px;background:rgba(255,255,255,.75)}
  .contacts{position:absolute;left:310px;top:234px;color:var(--ink-light);font-size:12.5px;list-style:none}
  .contacts li{display:flex;align-items:center;gap:7px;margin-bottom:8px}
  .contacts svg{width:15px;height:15px;flex:none}
  .web-strip{
    position:absolute;left:0;right:0;bottom:0;height:28px;background:var(--rim-grey);
    color:var(--ink-light);font-size:12px;letter-spacing:5px;
    display:flex;align-items:center;justify-content:center;
  }

  /* back */
  .back .web{position:absolute;left:34px;top:52px;color:var(--ink-light);font-size:12px;letter-spacing:5px;transform:rotate(-9deg);transform-origin:left top}
  .back .brand{left:168px;top:172px}
  .socials{position:absolute;left:134px;top:170px;display:flex;flex-direction:column;gap:7px}
  .social-square{width:15px;height:15px;border-radius:3px;background:var(--brown-deep)}
</style>
</head>
<body>

  <section class="card front" aria-label="Card front">
    <svg class="card-bg" viewBox="0 0 560 320" aria-hidden="true">
      <defs>
        <linearGradient id="brownFront" x1="0" y1="1" x2="1" y2="0">
          <stop offset="0" stop-color="#5a2c02"/>
          <stop offset="1" stop-color="#8b4a17"/>
        </linearGradient>
      </defs>
      <rect width="560" height="320" fill="url(#brownFront)"/>
      <path d="M0,0 H556 Q516,246 0,256 Z" fill="var(--rim-grey)"/>
      <path d="M0,0 H548 Q508,238 0,248 Z" fill="var(--paper-shade)"/>
      <path d="M0,0 H540 Q500,230 0,240 Z" fill="var(--paper)"/>
    </svg>

    <div class="brand">
      <div class="brand-name">Bram Keystone Homes</div>
      <div class="brand-slogan">- HOME RENOVATIONS - CUSTOM PROJECT DESIGN -</div>
    </div>

    <div class="person">
      <div class="person-name">Ludovic Entrasse</div>
      <div class="person-role">President / Ceo</div>
    </div>
    <div class="divider"></div>
    <ul class="contacts">
      <li>
        <svg viewBox="0 0 16 16" aria-hidden="true"><circle cx="8" cy="8" r="8" fill="#fff"/><rect x="5.5" y="3.5" width="5" height="9" rx="1" fill="none" stroke="#663300" stroke-width="1.3"/></svg>
        519.604.3087
      </li>
      <li>
        <svg viewBox="0 0 16 16" aria-hidden="true"><circle cx="8" cy="8" r="8" fill="#fff"/><rect x="4" y="5" width="8" height="6" fill="none" stroke="#663300" stroke-width="1.2"/><path d="M4 5 L8 8.5 L12 5" fill="none" stroke="#663300" stroke-width="1.2"/></svg>
        info@bramkeystone.ca
      </li>
    </ul>
    <div class="web-strip">www.bramkeystone.ca</div>
  </section>

  <section class="card back" aria-label="Card back">
    <svg class="card-bg" viewBox="0 0 560 320" aria-hidden="true">
      <defs>
        <linearGradient id="brownBack" x1="0" y1="1" x2="1" y2="0">
          <stop offset="0" stop-color="#5a2c02"/>
          <stop offset="1" stop-color="#8b4a17"/>
        </linearGradient>
      </defs>
      <rect width="560" height="320" fill="url(#brownBack)"/>
      <path d="M0,320 V122 Q170,16 560,4 V320 Z" fill="var(--rim-grey)"/>
      <path d="M0,320 V130 Q178,26 560,12 V320 Z" fill="var(--paper-shade)"/>
      <path d="M0,320 V138 Q186,36 560,20 V320 Z" fill="var(--paper)"/>
    </svg>

    <div class="web">www.bramkeystone.ca</div>
    <div class="socials" aria-label="Social links">
      <span class="social-square"></span>
      <span class="social-square"></span>
      <span class="social-square"></span>
    </div>
    <div class="brand">
      <div class="brand-name">Bram Keystone Homes</div>
      <div class="brand-slogan">- HOME RENOVATIONS - CUSTOM PROJECT DESIGN -</div>
    </div>
  </section>

</body>
</html>
```